Automotive component supplier needs a business card design

We need a business card design for our company called Velran Global Components Ltd based in the UK. We are a supplier of interior and exterior components to premium car manufacturers such as Corvel Ashby, Hadley Fenn, Marquist and Tavarelli. We would like to see a modern business card design that uses the colour blue.

Target Market(s)

Premium automotive car manufacturers.

Industry/Entity Type

Automotive

Contact Information for Business Card

Company Name : Velran Global Components Limited
Address: 17 Marlow Yard, Upper Heath, Warwick, CV31 8QL, United Kingdom
Web Address : www.velrancomponents-example.co.uk

Font styles to use
Other font styles liked:
• Helvetica

Colors
3176b5
0255a3
85acd3
cfdeed
cee9f5
85cae6
34a6d7
0692cd
9bcb3c

Requirements
Must have
• Clear company logo and a mixture of blue colours.
Nice to have
• A high quality modern image.
Should not have
• Multiple colours.

```html
<!DOCTYPE html>
<html lang="en">
<head>
<meta charset="utf-8">
<title>Velran Global Components – Business Card</title>
<link rel="stylesheet" href="https://fonts.googleapis.com/css2?family=Arimo:wght@400;700&family=Oswald:wght@500;600&display=swap">
<style>
  :root {
    --blue: #0692cd;
    --blue-deep: #0255a3;
    --blue-mid: #34a6d7;
    --green: #9bcb3c;
    --paper: #ffffff;
    --ink: #1d1d1d;
    --stage: #2a2b2d;
  }
  * { margin: 0; padding: 0; box-sizing: border-box; }
  html, body { width: 1200px; height: 900px; overflow: hidden; }
  body {
    background: var(--stage);
    font-family: "Arimo", Helvetica, Arial, sans-serif;
    display: flex;
    align-items: center;
    justify-content: center;
    gap: 50px;
  }
  .card {
    position: relative;
    width: 525px;
    height: 300px;
    border-radius: 26px;
    background: var(--paper);
    overflow: hidden;
  }
  .stripe {
    position: absolute;
    left: 0; right: 0; bottom: 0;
    height: 20px;
    display: flex;
  }
  .stripe span { display: block; height: 100%; }
  .stripe .blue { background: var(--blue); }
  .stripe .green { background: var(--green); }

  /* front */
  .front .brand {
    position: absolute;
    left: 0; right: 0; top: 120px;
    text-align: center;
  }
  .front .brand-name {
    font-weight: 700;
    font-size: 27px;
    letter-spacing: 1px;
    color: var(--blue);
    text-transform: uppercase;
    white-space: nowrap;
  }

  /* back */
  .back .top-panel {
    position: absolute;
    left: 0; right: 0; top: 0;
    height: 158px;
    background: linear-gradient(90deg, var(--blue) 0%, var(--blue-mid) 100%);
  }
  .back .brand {
    position: absolute;
    right: 30px; top: 34px;
  }
  .back .brand-name {
    font-weight: 700;
    font-size: 15px;
    letter-spacing: 0.6px;
    color: var(--paper);
    text-transform: uppercase;
    white-space: nowrap;
  }
  .person {
    position: absolute;
    left: 34px; top: 84px;
    color: var(--paper);
    font-family: "Oswald", "Arial Narrow", sans-serif;
    text-transform: uppercase;
  }
  .person-name { font-size: 30px; font-weight: 600; line-height: 1; letter-spacing: 0.5px; }
  .person-role { font-size: 16px; font-weight: 500; margin-top: 4px; letter-spacing: 0.5px; }
  .contact {
    position: absolute;
    left: 34px; top: 170px;
    font-size: 12px;
    color: var(--ink);
    line-height: 1.3;
  }
  .address { margin-bottom: 6px; }
  .contact-list { list-style: none; }
  .contact-list li { display: flex; align-items: center; gap: 9px; white-space: nowrap; }
  .contact-list svg { width: 11px; height: 11px; fill: var(--blue-deep); flex: none; }
  .web-domain { color: var(--blue); }
</style>
</head>
<body>

<section class="card front" aria-label="Card front">
  <div class="brand">
    <span class="brand-name">Velran Global Components</span>
  </div>
  <div class="stripe">
    <span class="blue" style="width:44%"></span>
    <span class="green" style="width:28%"></span>
    <span class="blue" style="width:28%"></span>
  </div>
</section>

<section class="card back" aria-label="Card back">
  <div class="top-panel"></div>
  <div class="brand">
    <span class="brand-name">Velran Global Components</span>
  </div>
  <div class="person">
    <div class="person-name">Daniel Morrow</div>
    <div class="person-role">CEO/Founder</div>
  </div>
  <div class="contact">
    <p class="address">17 Marlow Yard, Upper Heath,<br>Warwick, CV31 8QL, UK</p>
    <ul class="contact-list">
      <li>
        <svg viewBox="0 0 16 16"><path d="M3 1l3 1 1 4-2 1c1 2 2 3 4 4l1-2 4 1 1 3-2 2C7 15 1 9 1 3z"/></svg>
        01926 555 0142
      </li>
      <li>
        <svg viewBox="0 0 16 16"><path d="M4 0h8a1 1 0 011 1v14a1 1 0 01-1 1H4a1 1 0 01-1-1V1a1 1 0 011-1zm1 2v10h6V2zm3 11a1 1 0 100 2 1 1 0 000-2z"/></svg>
        07700 900 418
      </li>
      <li>
        <svg viewBox="0 0 16 16"><path d="M0 3h16v1L8 9 0 4zm0 3l8 5 8-5v7H0z"/></svg>
        d.morrow@velran-example.co.uk
      </li>
      <li>
        <svg viewBox="0 0 16 16"><circle cx="8" cy="8" r="8"/></svg>
        <span>www.<span class="web-domain">velrancomponents-example</span>.co.uk</span>
      </li>
    </ul>
  </div>
  <div class="stripe">
    <span class="blue" style="width:44%"></span>
    <span class="green" style="width:30%"></span>
    <span class="blue" style="width:26%"></span>
  </div>
</section>

</body>
</html>
```